Harborline Renewal Business Card Design

Professional and clean design. The design colors should flow with the logo. Two-sided card with the website on the back which is:

www.HarborlineRenewal.example.

"Specializing in Water Damage Restoration"

On the front I need the name, email, phone, and logo.

Name: Darnell Quisby
Email: Darnell@HarborlineRenewal.example
Phone: 555-318-2046 for now

I only have the Preview and Thumbnail right now but should have the source files uploaded within a day or two.

Target Market(s)

Flood victims, home owners with water damage from busted pipes etc...

Industry/Entity Type

Business

Contact Information for Business Card

Name: Darnell Quisby

Font styles to use
Serif
Sans Serif

Requirements
Must have
• Business Card Details Info

```html
<!DOCTYPE html>
<html lang="en">
<head>
<meta charset="utf-8">
<title>Harborline Renewal Business Card</title>
<link rel="stylesheet" href="https://fonts.googleapis.com/css2?family=Cinzel:wght@400&family=Open+Sans:wght@400;600&display=swap">
<style>
  :root {
    --backdrop: #ece7df;
    --card-white: #ffffff;
    --card-edge: #c9c9c9;
    --brand-blue: #2b97d4;
    --strip-blue: #5dc4ef;
    --ink-dark: #1e2c38;
    --ink-light: #ffffff;
  }
  * { box-sizing: border-box; margin: 0; padding: 0; }
  html, body {
    width: 1200px;
    height: 1188px;
    overflow: hidden;
    background: var(--backdrop);
  }
  .canvas { position: relative; width: 1200px; height: 1188px; }

  .card {
    position: absolute;
    width: 904px;
    height: 515px;
    border-radius: 42px;
    overflow: hidden;
  }

  /* Front side */
  .card-front {
    left: 238px;
    top: 51px;
    background: var(--card-white);
    border: 2px solid var(--card-edge);
  }
  .front-brand {
    position: absolute;
    left: 30px;
    top: 165px;
    width: 420px;
    text-align: center;
  }
  .brand-dot {
    display: block;
    margin: 0 auto;
    border-radius: 50%;
  }
  .front-brand .brand-dot {
    width: 82px;
    height: 82px;
    margin-bottom: 22px;
    background: var(--brand-blue);
  }
  .brand-name {
    display: block;
    font-family: "Open Sans", sans-serif;
    font-weight: 600;
    line-height: 1.1;
  }
  .front-brand .brand-name {
    font-size: 34px;
    color: var(--brand-blue);
  }

  .web-strip {
    position: absolute;
    left: 450px;
    top: 73px;
    width: 43px;
    height: 367px;
    background: var(--strip-blue);
  }
  .web-strip .web-address {
    position: absolute;
    left: 50%;
    top: 50%;
    transform: translate(-50%, -50%) rotate(-90deg);
    white-space: nowrap;
    font-family: "Open Sans", sans-serif;
    font-size: 19px;
    color: var(--ink-dark);
  }

  .contact-panel {
    position: absolute;
    left: 497px;
    top: 73px;
    width: 407px;
    height: 367px;
    background: var(--brand-blue);
    color: var(--ink-light);
    padding: 38px 0 0 16px;
  }
  .contact-panel .person-name {
    font-family: "Cinzel", serif;
    font-weight: 400;
    font-size: 33px;
    line-height: 1.1;
    letter-spacing: 1px;
  }
  .contact-panel .person-title {
    font-family: "Cinzel", serif;
    font-size: 28px;
    line-height: 1.1;
    letter-spacing: 2px;
    margin-top: 2px;
  }
  .contact-panel .address {
    font-family: "Open Sans", sans-serif;
    font-size: 18px;
    line-height: 26px;
    margin-top: 38px;
  }
  .contact-panel .contact-list {
    list-style: none;
    font-family: "Open Sans", sans-serif;
    font-size: 18px;
    line-height: 31px;
    margin-top: 27px;
  }
  .contact-list li { display: flex; align-items: center; gap: 10px; }
  .contact-list svg { width: 16px; height: 16px; flex: none; fill: var(--ink-light); }

  /* Back side */
  .card-back {
    left: 31px;
    top: 624px;
    background: var(--brand-blue);
    color: var(--ink-light);
  }
  .back-brand {
    position: absolute;
    left: 0;
    top: 70px;
    width: 904px;
    text-align: center;
  }
  .back-brand .brand-dot {
    width: 210px;
    height: 210px;
    margin-bottom: 22px;
    background: var(--ink-light);
  }
  .back-brand .brand-name {
    font-size: 36px;
    color: var(--ink-light);
  }
  .tagline {
    position: absolute;
    left: 0;
    top: 398px;
    width: 904px;
    text-align: center;
    font-family: "Cinzel", serif;
    font-size: 24px;
    letter-spacing: 1px;
  }
</style>
</head>
<body>
<main class="canvas">
  <section class="card card-front" aria-label="Business card front">
    <div class="front-brand">
      <span class="brand-dot"></span>
      <span class="brand-name">Harborline Renewal</span>
    </div>
    <div class="web-strip"><span class="web-address">www.harborlinerenewal.example</span></div>
    <div class="contact-panel">
      <h1 class="person-name">Darnell Quisby</h1>
      <p class="person-title">Title</p>
      <p class="address">Street Name, City Name<br>Zipcode-12345</p>
      <ul class="contact-list">
        <li>
          <svg viewBox="0 0 16 16" aria-hidden="true"><path d="M3.6 1.2l2.3 2.4-1.3 2a8.5 8.5 0 0 0 5.8 5.8l2-1.3 2.4 2.3-1.6 2.4C7.2 14.8 1.2 8.8 1.2 2.8z"/></svg>
          555-318-2046
        </li>
        <li>
          <svg viewBox="0 0 16 16" aria-hidden="true"><path d="M1 4h14v9H1z M1 4l7 5 7-5" fill="none" stroke="#fff" stroke-width="1.6"/></svg>
          darnell@harborlinerenewal.example
        </li>
      </ul>
    </div>
  </section>

  <section class="card card-back" aria-label="Business card back">
    <div class="back-brand">
      <span class="brand-dot"></span>
      <span class="brand-name">Harborline Renewal</span>
    </div>
    <p class="tagline">Specializing in Water Damage Restoration</p>
  </section>
</main>
</body>
</html>
```